BRELWINCare.co.uk - Mental Health Clinic for Child and Adolescents

Updated 29/01/2018***
I am not sure you guys are getting the idea regards to the opening page / homescreen layout. Can you look at the new images I have uploaded (page 5, 6 and 7) These are some of the layouts I like but to incorporate my chosen images, with the BRELWIN commissioner, buttons and a sliding header bar.
I have written a strong brief, I am looking for a website, preferably wordpress as i know they are easy to maintain. I am looking for a one page site, with the top / opening page being full screen image with drop down categories. I have made a rough design, see full brief in word doc attached, there is some freedom to play around with the design aspect but it will need to relay all the content provided. I like a minimal feel. I have also attached some images that may be useful, but will need a new logo for BRELWIN Care. I have attached some logo idea's, it is up to you decide whether you want to use them.
I would prefer the homepage as full screen image, and the categories offered as a drop down or over the main image.
I have also attached linked to some competitors websites:
https://www.vorimant-health.co.uk/
http://www.qlbn.org.uk/
Industry/Entity Type
Clinic
Number of Pages Required
1 page
Font styles to use
Look and feel
Each slider illustrates characteristics of the customer's brand and the style your logo design should communicate.

```html
<!DOCTYPE html>
<html lang="en">
<head>
<meta charset="utf-8">
<title>BRELWIN Care – Family Therapists &amp; Contact</title>
<link href="https://fonts.googleapis.com/css2?family=Open+Sans:wght@400;600;700&display=swap" rel="stylesheet">
<style>
  :root {
    --ink: #2b3640;
    --text: #333a40;
    --muted-bg: #f2f2f2;
    --panel-bg: #e9e9ea;
    --contact-bg: #f7f7f8;
    --gap-bg: #eeeeee;
    --footer-bg: #263238;
    --footer-text: #ffffff;
    --link: #2a3fb0;
    --edge: #3a4148;
  }
  * { box-sizing: border-box; margin: 0; padding: 0; }
  html, body { width: 1200px; height: 1200px; overflow: hidden; }
  body {
    position: relative;
    font-family: "Open Sans", Arial, sans-serif;
    color: var(--text);
    background: var(--muted-bg);
  }
  .page-edge { position: absolute; left: 0; top: 0; width: 4px; height: 1148px; background: var(--edge); z-index: 5; }

  /* Services continuation */
  .services-tail { position: absolute; left: 0; top: 0; width: 1200px; height: 168px; background: var(--muted-bg); }
  .services-tail .photo {
    position: absolute; left: 622px; top: 0; width: 578px; height: 161px;
    background: linear-gradient(90deg, #5f7896 0%, #8a7a62 45%, #b59c7a 70%, #d8c2a8 100%);
  }

  .bullet-list { list-style: none; position: absolute; }
  .bullet-list li { position: relative; font-size: 17.6px; line-height: 28.8px; }
  .bullet-list li::before { content: "•"; position: absolute; left: -34px; font-size: 14px; }
  .services-tail .bullet-list { left: 104px; top: -4px; }

  /* Family therapists */
  .family { position: absolute; left: 0; top: 168px; width: 1200px; height: 432px; background: var(--panel-bg); }
  .family .photo {
    position: absolute; left: 4px; top: 0; width: 576px; height: 432px;
    background: linear-gradient(120deg, #d9d5cf 0%, #efeeec 40%, #c9b49b 70%, #9a7b5e 100%);
  }
  .family h2 {
    position: absolute; left: 626px; top: 26px; width: 508px;
    font-size: 30px; font-weight: 700; color: var(--ink); letter-spacing: 0.3px;
    padding-bottom: 4px; border-bottom: 2px solid var(--ink);
  }
  .family p { position: absolute; left: 626px; top: 78px; width: 510px; font-size: 17.6px; line-height: 28.8px; }
  .family .bullet-list { left: 669px; top: 182px; }

  /* Contact */
  .contact { position: absolute; left: 0; top: 600px; width: 1200px; height: 530px; background: var(--contact-bg); }
  .contact .backdrop {
    position: absolute; left: 48px; top: 120px; width: 1104px; height: 410px;
    background: linear-gradient(90deg, #f3f0ec 0%, #efe9e2 35%, #f2ede6 65%, #f4f2ee 100%);
    opacity: 0.9;
  }
  .contact h2 {
    position: absolute; left: 0; top: 60px; width: 1200px; text-align: center;
    font-size: 26px; font-weight: 600; color: var(--ink); letter-spacing: 0.5px;
  }
  .contact .rule { position: absolute; left: 549px; top: 103px; width: 104px; height: 3px; background: var(--ink); }
  .contact-info { position: absolute; left: 62px; top: 150px; width: 560px; font-size: 13.6px; line-height: 24px; }
  .contact-info .intro { margin-bottom: 14px; }
  .contact-info dt { font-weight: 700; line-height: 19px; }
  .contact-info dd { line-height: 19px; margin-bottom: 16px; }
  .contact-info .email { font-weight: 700; line-height: 19px; }
  .contact-info .email a { color: var(--link); text-decoration: none; font-weight: 400; }
  .contact .map {
    position: absolute; left: 676px; top: 158px; width: 486px; height: 300px;
    background: linear-gradient(160deg, #ececec 0%, #e4e4e4 45%, #efe3b8 55%, #e6e6e6 70%, #ededed 100%);
  }

  .gap-band { position: absolute; left: 0; top: 1130px; width: 1200px; height: 18px; background: var(--gap-bg); }
  .site-footer {
    position: absolute; left: 0; top: 1148px; width: 1200px; height: 52px;
    background: var(--footer-bg); color: var(--footer-text);
    font-size: 13.6px; text-align: center; line-height: 52px;
  }
</style>
</head>
<body>
  <div class="page-edge"></div>

  <section class="services-tail">
    <ul class="bullet-list">
      <li>Trauma</li>
      <li>Body Dysmorphia</li>
      <li>Addiction</li>
    </ul>
    <div class="photo" role="img" aria-label="Photo of a therapist taking notes beside a young girl in a colourful striped top"></div>
  </section>

  <section class="family">
    <div class="photo" role="img" aria-label="Photo of a therapist in a white shirt talking with a boy in a checked shirt by a fireplace"></div>
    <h2>Family Therapists</h2>
    <p>We can offer high quality that will be carried out by fully qualified Family Therapists therapist. Our therapists are trained to work with the following:</p>
    <ul class="bullet-list">
      <li>Anxiety and Depression</li>
      <li>Eating Disorders</li>
      <li>Trauma</li>
      <li>Body Dysmorphia</li>
      <li>Addiction</li>
    </ul>
  </section>

  <section class="contact">
    <div class="backdrop" role="img" aria-label="Faint background photo of smiling teenagers sitting together on a sofa"></div>
    <h2>CONTACT US</h2>
    <div class="rule"></div>
    <div class="contact-info">
      <p class="intro">Lorem ipsum dolor sit amet, consectetur adipiscing elit. Cras sed felis tempor, dictum diam non, egestas sapien. Nulla vitae sem gravida, imperdiet nisl sed, luctus nisl.</p>
      <dl>
        <dt>Phone Number:</dt>
        <dd>0203 555 0182</dd>
        <dt>Address:</dt>
        <dd>Larchmont Suite 2B, 41-47 Fenwick Road, London, E17 4RT</dd>
        <dt>Opening Times:</dt>
        <dd>9am – 5pm Mon-Fri</dd>
      </dl>
      <p class="email">Email <span style="font-weight:400">–</span> <a href="mailto:enquiry@brelwincare.co.uk">enquiry@brelwincare.co.uk</a></p>
    </div>
    <div class="map" role="img" aria-label="Street map showing the clinic location near a main ring road"></div>
  </section>

  <div class="gap-band"></div>
  <footer class="site-footer">Copyright 2018 brelwincare.co.uk</footer>
</body>
</html>
```